need a clean, modern job advertisement designed for social media (Facebook & Instagram).

The post is to advertise two positions:
• Leading Hand Boilermaker
• Dragline Fitter
We want the design to match our KPR Site Services branding: blue, white, strong, professional, mining-industry style.
What the design should include:
Bold headline: “WE’RE HIRING”
Sub-headline: “Leading Hand Boilermaker & Dragline Fitter”
Key points:
• Tallon Basin based
• Dragline & shovel maintenance
• Great pay + long-term work
• Locally owned & operated
KPR logo placed cleanly
Space for 1–2 images (boilermaking or dragline work)
Design style:
Strong and industrial
Blue/white colour scheme
Easy to read at a glance
Suitable for a square 1080×1080 design

```html
<!DOCTYPE html>
<html lang="en">
<head>
<meta charset="UTF-8">
<title>KPR Site Services – We're Hiring</title>
<link href="https://fonts.googleapis.com/css2?family=Abril+Fatface&family=Poppins:wght@400;600;700;800&display=swap" rel="stylesheet">
<style>
  :root{
    --page-bg:#dcfdfd;
    --royal:#1f3ff5;
    --navy:#0d1438;
    --deep:#111a4a;
    --cyan:#55d6f4;
    --white:#ffffff;
    --silver-top:#f4f6f8;
    --silver-bottom:#8f969c;
  }
  *{margin:0;padding:0;box-sizing:border-box}
  html,body{width:1200px;height:720px;overflow:hidden;background:var(--page-bg)}
  .post{
    position:absolute;left:265px;top:25px;width:670px;height:670px;overflow:hidden;
    background:linear-gradient(100deg,var(--royal) 0%,#1e3be0 30%,var(--deep) 62%,var(--navy) 100%);
    box-shadow:0 4px 14px rgba(0,60,60,.25);
    font-family:"Poppins",sans-serif;color:var(--white);
  }
  .site-photo{
    position:absolute;left:0;top:290px;width:360px;height:380px;
    background:linear-gradient(175deg,rgba(40,90,200,0) 0%,#2f5f8a 25%,#1f2f45 50%,#b9ad45 78%,#d8c95a 100%);
    -webkit-mask-image:linear-gradient(90deg,#000 70%,transparent 100%);
            mask-image:linear-gradient(90deg,#000 70%,transparent 100%);
  }
  .brand{
    position:absolute;left:40px;top:80px;width:210px;
    display:flex;align-items:center;gap:10px;
    font-weight:700;font-size:24px;line-height:1.05;color:var(--white);
  }
  .brand-dot{width:34px;height:34px;border-radius:50%;background:var(--cyan);flex:none}
  .headline{position:absolute;right:53px;top:22px;text-align:right;font-family:"Abril Fatface",serif;line-height:.86}
  .headline .were{
    display:block;font-size:102px;letter-spacing:-1px;
    background:linear-gradient(180deg,var(--silver-top),var(--silver-bottom));
    -webkit-background-clip:text;background-clip:text;color:transparent;
  }
  .headline .hiring{display:block;font-size:100px;color:var(--cyan);letter-spacing:-1px;margin-top:6px}
  .roles{
    position:absolute;right:53px;top:214px;text-align:right;
    font-weight:700;font-size:32px;line-height:1.1;
  }
  .perks{position:absolute;right:52px;top:309px;list-style:none;display:flex;flex-direction:column;align-items:flex-end;gap:24px}
  .perk{
    height:18px;display:flex;align-items:center;gap:4px;
    padding:0 4px 0 14px;background:var(--cyan);
    clip-path:polygon(8px 0,100% 0,100% 100%,0 100%);
    font-size:15px;line-height:1;color:var(--white);
  }
  .perk svg{width:10px;height:10px}
  .gallery{position:absolute;left:273px;top:479px;width:346px;height:91px}
  .shot{position:absolute;top:0;width:180px;height:91px;clip-path:polygon(18px 0,100% 0,calc(100% - 18px) 100%,0 100%);background:var(--cyan)}
  .shot .fill{position:absolute;inset:2px 3px;clip-path:polygon(16px 0,100% 0,calc(100% - 16px) 100%,0 100%)}
  .shot-weld{left:0}
  .shot-weld .fill{background:linear-gradient(120deg,#1b2450,#2b3f8a 55%,#0c1230)}
  .shot-grind{left:162px}
  .shot-grind .fill{background:linear-gradient(120deg,#2a2622,#6b4a2a 55%,#1a1612)}
  .contact{position:absolute;right:52px;top:598px;text-align:right}
  .phone{display:flex;align-items:center;justify-content:flex-end;gap:8px;font-weight:800;font-size:29px;color:var(--cyan);line-height:1}
  .web{display:flex;align-items:center;justify-content:flex-end;gap:8px;font-size:15px;margin-top:6px;line-height:1}
</style>
</head>
<body>
<main class="post">
  <div class="site-photo" role="img" aria-label="Photo of a worn yellow hard hat in front of a mine site and coastal view"></div>

  <div class="brand"><span class="brand-dot"></span><span>KPR Site Services</span></div>

  <h1 class="headline"><span class="were">WE’RE</span><span class="hiring">HIRING</span></h1>

  <h2 class="roles">Leading Hand Boilermaker<br>&amp; Dragline Fitter</h2>

  <ul class="perks">
    <li class="perk">Tallon Basin based <svg viewBox="0 0 10 10"><circle cx="5" cy="5" r="4.2" fill="none" stroke="#fff" stroke-width="1"/><path d="M3 5.2l1.4 1.4L7.2 3.8" fill="none" stroke="#fff" stroke-width="1"/></svg></li>
    <li class="perk">Dragline &amp; shovel maintenance <svg viewBox="0 0 10 10"><circle cx="5" cy="5" r="4.2" fill="none" stroke="#fff" stroke-width="1"/><path d="M3 5.2l1.4 1.4L7.2 3.8" fill="none" stroke="#fff" stroke-width="1"/></svg></li>
    <li class="perk">Great pay + long-term work <svg viewBox="0 0 10 10"><circle cx="5" cy="5" r="4.2" fill="none" stroke="#fff" stroke-width="1"/><path d="M3 5.2l1.4 1.4L7.2 3.8" fill="none" stroke="#fff" stroke-width="1"/></svg></li>
    <li class="perk">Locally owned &amp; operated <svg viewBox="0 0 10 10"><circle cx="5" cy="5" r="4.2" fill="none" stroke="#fff" stroke-width="1"/><path d="M3 5.2l1.4 1.4L7.2 3.8" fill="none" stroke="#fff" stroke-width="1"/></svg></li>
  </ul>

  <div class="gallery">
    <div class="shot shot-weld"><div class="fill" role="img" aria-label="Photo of a boilermaker welding at night"></div></div>
    <div class="shot shot-grind"><div class="fill" role="img" aria-label="Photo of a fitter grinding steel with sparks on a dragline"></div></div>
  </div>

  <div class="contact">
    <div class="phone">0400 555 017
      <svg width="12" height="22" viewBox="0 0 12 22"><rect x="1" y="1" width="10" height="20" rx="2" fill="none" stroke="#fff" stroke-width="1.5"/><line x1="4.5" y1="18" x2="7.5" y2="18" stroke="#fff" stroke-width="1.2"/></svg>
    </div>
    <div class="web">www.kprsiteservices.com
      <svg width="14" height="14" viewBox="0 0 14 14"><circle cx="7" cy="7" r="6" fill="#fff"/><path d="M1 7h12M7 1c-2.5 3-2.5 9 0 12M7 1c2.5 3 2.5 9 0 12" stroke="#0d1438" stroke-width=".9" fill="none"/></svg>
    </div>
  </div>
</main>
</body>
</html>
```